Banner ad design for Vorlix Display Ads

We are looking for a designer to develop a concept for banner ads for a Vorlix Display campaign we are building.

We have 3 business lines, shredding services, records management services and scanning services.

We are looking for 4 sets of ads to be created, one for each business line + one set that showcases all of our lines together.

For the design concepts, we would like to see a few sizes (banner, square, leaderboard, skyscraper, etc) for each.

The person chosen will then need to create the ads into all Vorlix supported sizes -- 20 sizes total for each set of ads as per the Vorlix size guidelines found on this page - https://help.vorlix.com/vorlix-ads/answer/5830417?hl=en&ref_topic=6402871#

A few items to note:
- Design should complement our existing brand/website look and feel (www.tamrock-dunes.ca)
- Each final ad must be 150Kb or less in size
- Final designs should be editable, meaning if we would like to change some copy in the design, we can do so using a well-known software (Canva, Photoshop/InDesign, etc)
- Some images are attached for use, but if you feel a different stock image is more suitable to to your design, please go ahead and use it.

Provided below is some messaging that can be used for each set of ads. Do not feel you need to use all of the messaging, it is provided for guidance.

SHREDDING SERVICES:

Possible Short Headline:
-- One-Time Shredding Services
-- Secure Shredding Services
-- Affordable On-Site Shredding

Possible Long Headline
-- Your Paper Can be Destroyed as Soon as the Next Business Day

Possible Descriptions:
-- TORV QQQ Certified On site shredding company. Service as soon as Next Day.
-- Secure and Affordable Toronto & GTA On-Site Shredding.
-- Certified, Affordable Office Shredding Since 2003.
-- Quick, no contact and affordable paper shredding services in Toronto & Southern Ontario.
-- Certified, Affordable Office Shredding Since 2003. Fast, no contact shredding service.

Call to Action
-- Get a Quote

RECORDS MANAGEMENT
Short Headline:
-- Off-site Records Storage
-- Records Management & Storage
-- Secure Records Storage
-- Records Management Services
-- Long Term Records Management
-- Document Storage Solutions

Possible Description
-- Local, Affordable Storage Solutions. Protect and Store your Documents in our Secure Facility
-- Local, Affordable Records Management Solutions. Store your Records in our Secure Facility
-- Certified, Affordable Document Storage Since 2004. Contact Us for a Free Quote!
-- Veltra+ Certified, Affordable Document Storage Since 2004. Contact Us for a Free Quote!

Call to Action
-- Get a Quote

SCANNING SERVICES

Short Headline:
-- Professional Scanning Company
-- Toronto & GTA Scanning Service
-- Document Scanning Services
-- Digital Conversion Services
-- Fast & Easy Retrieval

Description
-- Scan and documents and files with Professional scanning services from Tamrock-Dunes
-- Convert Your Paper Files to Electronic Files. Fast & Easy Retrieval.
-- Easily access your documents electronically with Document Scanning Services

Call to Action
-- Get a Quote

ALL SERVICES AD SET
Short Headline
-- Shred, Scan & Store Documents
-- Secure Shredding, Records Management and Scanning Services
-- #1 Document Management Company
-- Tamrock Dunes Shredding, Storage & Scanning

Description
-- Secure and Affordable Toronto & GTA On-Site Shredding, Document Storage & Scanning Company

Call to Action
-- Get a Quote

Font styles to use
Sans Serif

```html
<!DOCTYPE html>
<html lang="en">
<head>
<meta charset="utf-8">
<title>Tamrock-Dunes — Off-site Records Storage</title>
<link href="https://fonts.googleapis.com/css2?family=Arimo:wght@400;700&display=swap" rel="stylesheet">
<style>
  :root {
    --white: #ffffff;
    --brand-navy: #123a6b;
    --brand-blue: #1a9ad7;
    --panel-blue: #1b98d6;
    --cta-green: #27c264;
    --cta-border: #bff0d2;
    --photo-light: #e9e6e4;
    --photo-mid: #c9c3c0;
    --photo-dark: #8f8782;
  }
  * { margin: 0; padding: 0; box-sizing: border-box; }
  html, body { width: 1200px; height: 148px; overflow: hidden; background: var(--white); }
  .banner {
    position: relative;
    width: 1200px;
    height: 148px;
    display: flex;
    font-family: "Arimo", Arial, sans-serif;
  }
  .brand {
    width: 288px;
    background: var(--white);
    display: flex;
    flex-direction: column;
    justify-content: center;
    padding-left: 36px;
  }
  .brand-name {
    display: flex;
    align-items: center;
    gap: 8px;
    font-size: 29px;
    font-weight: 700;
    color: var(--brand-navy);
    letter-spacing: -0.5px;
    margin-top: 14px;
  }
  .brand-mark {
    width: 14px;
    height: 14px;
    background: var(--brand-blue);
  }
  .brand-tagline {
    font-size: 19px;
    font-weight: 400;
    color: var(--brand-navy);
    margin-top: 4px;
  }
  .photo {
    width: 327px;
    height: 148px;
    background: linear-gradient(120deg, var(--photo-dark) 0%, var(--photo-mid) 35%, var(--photo-light) 70%, var(--white) 100%);
  }
  .message {
    width: 456px;
    background: var(--panel-blue);
    color: var(--white);
    text-align: center;
    padding-top: 34px;
  }
  .headline {
    font-size: 31px;
    font-weight: 700;
    letter-spacing: -0.3px;
  }
  .description {
    font-size: 19.5px;
    line-height: 27px;
    margin-top: 13px;
  }
  .cta-panel {
    width: 129px;
    background: var(--cta-green);
    display: flex;
    align-items: center;
    justify-content: center;
  }
  .cta-button {
    width: 94px;
    height: 89px;
    border: 2px solid var(--cta-border);
    border-radius: 4px;
    color: var(--white);
    font-size: 22px;
    line-height: 28px;
    text-align: center;
    display: flex;
    align-items: center;
    justify-content: center;
    text-decoration: none;
  }
</style>
</head>
<body>
  <div class="banner">
    <div class="brand">
      <div class="brand-name"><span>tamrock-dunes</span><span class="brand-mark"></span></div>
      <div class="brand-tagline">Information Security</div>
    </div>
    <div class="photo" role="img" aria-label="Stacks of paper files and documents on an office desk with a hand resting on them"></div>
    <div class="message">
      <h1 class="headline">Off-site Records Storage</h1>
      <p class="description">Certified, Affordable Document Storage<br>Since 2004. Contact Us for a Free Quote!</p>
    </div>
    <div class="cta-panel">
      <a class="cta-button" href="#">Get a<br>Quote</a>
    </div>
  </div>
</body>
</html>
```